The Vantor Codex Book Cover

"The Vantor Codex" is a book I wrote with the slogan "Unlock Performance, Spark Engagement: Master the Art of Building Winning Cultures in Today's Hybrid World". The book is designed around a methodology that's mine and that I attached. I would love to see the graphic of the methodology integrated in the design in a very subtle way. Use colors from the model but the book cover should be catchy, modern and engaging to the eye.
Overall the book is about three key elements towards success:
- (Self) Directions (purpose)
- Human experience (people and psychological safety)
- Maximize engagement
The methodology is a FLOW so flow is something that could be incorporated as well in the concept.
Low design quality
Managers and Teams

```html
<!DOCTYPE html>
<html lang="en">
<head>
<meta charset="UTF-8">
<title>The Vantor Codex — Book Cover</title>
<link href="https://fonts.googleapis.com/css2?family=Montserrat:ital,wght@0,300;0,400;0,800;0,900;1,900&display=swap" rel="stylesheet">
<style>
  :root {
    --brand-blue: #1d3f8e;
    --ink: #1b1b1b;
    --paper: #ffffff;
    --night: #140c0e;
    --glow-blue: #4f9fd6;
    --glow-orange: #e2552c;
  }
  * { margin: 0; padding: 0; box-sizing: border-box; }
  html, body { width: 933px; height: 1200px; overflow: hidden; background: var(--paper); }
  .cover {
    position: relative;
    width: 933px;
    height: 1200px;
    background: var(--paper);
    font-family: 'Montserrat', sans-serif;
    overflow: hidden;
  }
  .hero-art {
    position: absolute;
    left: 0; top: 0;
    width: 933px; height: 509px;
    background:
      radial-gradient(circle at 52% 42%, rgba(79,159,214,0.75) 0, rgba(40,90,140,0.55) 26%, rgba(20,12,14,0) 44%),
      radial-gradient(circle at 78% 28%, rgba(255,170,90,0.9) 0, rgba(226,85,44,0.7) 14%, rgba(20,12,14,0) 42%),
      radial-gradient(circle at 14% 33%, rgba(79,159,214,0.55) 0, rgba(20,12,14,0) 14%),
      linear-gradient(100deg, #1c1416 0%, #2a1a1c 45%, #6e2a22 80%, #3a1816 100%);
  }
  .title {
    position: absolute;
    left: 0; width: 100%;
    text-align: center;
    line-height: 1;
  }
  .title-the {
    top: 549px;
    font-size: 74px;
    font-weight: 900;
    font-style: italic;
    letter-spacing: 0.22em;
    padding-left: 0.22em;
    color: var(--ink);
  }
  .title-main {
    top: 612px;
    font-size: 168px;
    font-weight: 900;
    font-style: italic;
    letter-spacing: -0.02em;
    color: var(--brand-blue);
  }
  .title-sub {
    top: 771px;
    font-size: 76px;
    font-weight: 900;
    letter-spacing: 0.42em;
    padding-left: 0.42em;
    color: var(--ink);
  }
  .tagline {
    position: absolute;
    left: 0; width: 100%;
    top: 930px;
    text-align: center;
  }
  .tagline-lead {
    font-size: 24px;
    font-weight: 800;
    color: var(--brand-blue);
    line-height: 30px;
  }
  .tagline-body {
    font-size: 24px;
    font-weight: 400;
    color: var(--ink);
    line-height: 30px;
    margin-top: 2px;
  }
  .author-band {
    position: absolute;
    left: 0; bottom: 0;
    width: 933px; height: 121px;
    background: var(--brand-blue);
    display: flex;
    align-items: center;
    justify-content: center;
  }
  .author-name {
    font-size: 54px;
    font-weight: 300;
    color: var(--paper);
    letter-spacing: 0.36em;
    padding-left: 0.36em;
    line-height: 1;
  }
</style>
</head>
<body>
  <main class="cover">
    <div class="hero-art" role="img" aria-label="Portraits of diverse team members linked by lines around a glowing digital globe, blue and orange light"></div>

    <h1>
      <span class="title title-the">THE</span>
      <span class="title title-main">VANTOR</span>
      <span class="title title-sub">CODEX</span>
    </h1>

    <div class="tagline">
      <p class="tagline-lead">UNLOCK PERFORMANCE, SPARK ENGAGEMENT</p>
      <p class="tagline-body">MASTER THE ART OF BUILDING WINNING CULTURES<br>IN TODAY'S HYBRID WORLD</p>
    </div>

    <footer class="author-band">
      <p class="author-name">RUBEN KALSTER</p>
    </footer>
  </main>
</body>
</html>
```